Project Lists Banner for HVAC ecommerce store

We want a banner that showcases our project list feature that will allow customers to create list of products that they can select and quickly order. this will be a middle of page banner. It will replace this banner - https://www.lumapixvault.com/image/84730295
Font: Noto Sans
Size: 938x300 px
Color Options: #0059E, #00BBE3, #C6C8C7
Text:
Create lists of frequently purchased SKU's for fast ordering.
- Warehouse Inventory
- Complete Systems
- Large Projects
- And More...
"Sign In" is the call to action button. make button with non rounded (square) boarders.
We don't want a computer screen in banner nor a person. You can look at our competitors below for ideas.
Our staging server is belfarq7.com for reference
Our competitors:
https://www.brantlowholdings.com/
https://www.folvexa.com/
https://www.zelbrk.com/
https://www.vostrel.com/index.html
HVAC, B2B
HVAC

```html
<!DOCTYPE html>
<html lang="en">
<head>
<meta charset="utf-8">
<title>Project Lists Banner</title>
<link rel="stylesheet" href="https://fonts.googleapis.com/css2?family=Noto+Sans:wght@300;400;600;700;800&display=swap">
<style>
  :root {
    --page: #ffffff;
    --navy: #0a3f7c;
    --navy-deep: #08356a;
    --navy-light: #1a5a9e;
    --cyan: #0fb5e3;
    --grey: #c6c8c7;
    --ink: #333a44;
    --muted: #8a9099;
    --line: #e1e4e8;
    --panel-bar: #0b4a96;
    --action: #f07a12;
    --icon: #5b6066;
  }
  * { box-sizing: border-box; margin: 0; padding: 0; }
  html, body { width: 1200px; height: 604px; overflow: hidden; background: var(--page); }
  body { font-family: "Noto Sans", sans-serif; position: relative; }

  .banner {
    position: absolute; left: 49px; top: 119px; width: 1103px; height: 353px;
    background: linear-gradient(100deg, var(--navy-deep) 0%, var(--navy) 55%, var(--navy-light) 100%);
    box-shadow: 0 4px 10px rgba(0,0,0,.35);
    overflow: hidden;
  }
  .banner__texture {
    position: absolute; inset: 0;
    background: radial-gradient(ellipse at 30% 60%, rgba(255,255,255,.05), transparent 60%),
                radial-gradient(ellipse at 80% 20%, rgba(255,255,255,.04), transparent 55%);
  }
  .headline {
    position: absolute; left: 37px; top: 28px; width: 540px;
    color: #fff; font-weight: 700; font-size: 29.6px; line-height: 36px; letter-spacing: -.1px;
  }
  .features { position: absolute; left: 37px; top: 117px; list-style: none; }
  .features li {
    display: flex; align-items: center; height: 40.5px;
    color: #fff; font-weight: 400; font-size: 29.6px;
  }
  .features svg { width: 22px; height: 22px; margin-right: 37px; flex: none; }
  .cta {
    position: absolute; left: 33px; top: 276px; width: 183px; height: 41px;
    background: var(--cyan); color: #fff; border-radius: 0;
    font-weight: 800; font-size: 26px; display: flex; align-items: center; justify-content: center;
    letter-spacing: .5px;
  }

  .app {
    position: absolute; left: 551px; top: 36px; width: 520px; height: 285px;
    background: #fff; font-size: 5px; color: var(--ink);
  }
  .app__nav { position: absolute; left: 6px; top: 20px; width: 96px; height: 130px; border: 1px solid var(--line); }
  .app__nav h4 { font-size: 6px; font-weight: 600; padding: 5px 4px; border-bottom: 1px solid var(--line); }
  .app__nav ul { list-style: none; padding: 4px; }
  .app__nav li { font-size: 4.2px; line-height: 9.8px; color: #555; text-transform: uppercase; }
  .app__nav li.is-active { color: var(--panel-bar); }
  .import { position: absolute; left: 6px; top: 155px; width: 96px; height: 100px; border: 1px solid var(--line); padding: 6px; }
  .import h5 { font-size: 4.8px; font-weight: 600; }
  .import__drop { margin-top: 5px; border: 1px dashed #999; height: 62px; padding: 4px; text-align: center; font-size: 4px; line-height: 6px; color: #555; }
  .import__btn { display: block; margin: 3px auto; width: 50px; height: 8px; background: var(--panel-bar); color: #fff; font-size: 4px; line-height: 8px; }
  .import__link { color: var(--panel-bar); text-decoration: underline; }
  .import__tut { display: block; margin: 5px auto 0; width: 52px; height: 9px; background: var(--action); color: #fff; text-align: center; font-size: 4px; line-height: 9px; }

  .app__main { position: absolute; left: 108px; top: 0; right: 6px; }
  .app__title { position: absolute; top: 20px; left: 0; font-size: 9px; font-weight: 600; color: #444; }
  .app__print { position: absolute; top: 23px; right: 0; font-size: 4.4px; color: var(--panel-bar); }
  .project-bar { position: absolute; top: 50px; left: 0; right: 0; height: 11px; background: var(--panel-bar); color: #fff; display: flex; justify-content: space-between; align-items: center; padding: 0 5px; font-size: 5px; font-weight: 700; }
  .project-bar span:last-child { font-weight: 400; font-size: 4px; }
  .field { position: absolute; border: 1px solid #ccc; height: 14px; font-size: 4.4px; padding: 4px 5px; color: #666; }
  .btn-sm { position: absolute; height: 14px; font-size: 4.4px; color: #fff; display: flex; align-items: center; justify-content: center; }

  .grid { position: absolute; top: 168px; left: 0; right: 0; }
  .grid__head, .grid__row { display: flex; align-items: center; border-bottom: 1px solid var(--line); }
  .grid__head { height: 12px; background: #f4f5f7; font-weight: 600; font-size: 4.4px; }
  .grid__row { height: 23px; }
  .c-box { width: 14px; padding-left: 3px; }
  .c-box i { display: block; width: 6px; height: 6px; border: 1px solid #888; }
  .c-mark { width: 22px; font-size: 4px; font-weight: 700; color: #222; }
  .c-name { width: 222px; font-size: 4.2px; line-height: 6px; }
  .c-name b { font-weight: 600; display: block; }
  .c-name small { color: var(--muted); font-size: 3.8px; }
  .c-qty { width: 54px; display: flex; align-items: center; gap: 2px; }
  .c-qty i { width: 12px; height: 12px; background: var(--icon); color: #fff; font-style: normal; font-size: 7px; line-height: 12px; text-align: center; }
  .c-qty span { width: 12px; text-align: center; font-size: 4.2px; }
  .c-sell { width: 38px; font-size: 4.2px; }
  .c-my { width: 40px; font-size: 4.2px; display: flex; align-items: center; gap: 2px; }
  .c-my span { border: 1px solid #ccc; width: 26px; height: 11px; line-height: 9px; padding-left: 2px; }
  .c-del { width: 10px; display: flex; align-items: center; }
  .c-del svg { width: 5px; height: 6px; }
</style>
</head>
<body>
  <section class="banner">
    <div class="banner__texture" role="img" aria-label="Faint large brand shape decoration in deep blue"></div>

    <h1 class="headline">Create Project Lists of frequency purchased SKU's for fast ordering.</h1>

    <ul class="features">
      <li><svg viewBox="0 0 24 24" aria-hidden="true"><g stroke="#4fc6ee" stroke-width="2" stroke-linecap="round" fill="none"><path d="M12 1v22M2.5 6.5l19 11M2.5 17.5l19-11"/><path d="M9 3l3 3 3-3M9 21l3-3 3 3M3 10l4-1-1-4M21 14l-4 1 1 4M3 14l4 1-1 4M21 10l-4-1 1-4"/></g></svg>Warehouse Inventory</li>
      <li><svg viewBox="0 0 24 24" aria-hidden="true"><g stroke="#4fc6ee" stroke-width="2" stroke-linecap="round" fill="none"><path d="M12 1v22M2.5 6.5l19 11M2.5 17.5l19-11"/><path d="M9 3l3 3 3-3M9 21l3-3 3 3M3 10l4-1-1-4M21 14l-4 1 1 4M3 14l4 1-1 4M21 10l-4-1 1-4"/></g></svg>Complete Systems</li>
      <li><svg viewBox="0 0 24 24" aria-hidden="true"><g stroke="#4fc6ee" stroke-width="2" stroke-linecap="round" fill="none"><path d="M12 1v22M2.5 6.5l19 11M2.5 17.5l19-11"/><path d="M9 3l3 3 3-3M9 21l3-3 3 3M3 10l4-1-1-4M21 14l-4 1 1 4M3 14l4 1-1 4M21 10l-4-1 1-4"/></g></svg>Large Projects And More...</li>
    </ul>

    <a class="cta">SIGN IN</a>

    <div class="app">
      <nav class="app__nav">
        <h4>My Account</h4>
        <ul>
          <li>Dashboard</li><li>Profile</li><li>Address Book</li><li>Manage Users</li>
          <li>Invoice History</li><li>Order History</li><li>Statements</li><li>My Quotes</li>
          <li>Favorites</li><li class="is-active">Project Lists</li>
        </ul>
      </nav>
      <div class="import">
        <h5>Import Project Lists</h5>
        <div class="import__drop">
          Drag and drop a .CSV file here, or select file from your computer.
          <span class="import__btn">Choose File</span>
          <span class="import__link">Download Sample CSV</span>
        </div>
        <span class="import__tut">Tutorial</span>
      </div>

      <div class="app__main">
        <div class="app__title">Project Lists</div>
        <div class="app__print">Print Projects</div>
        <div class="project-bar"><span>Project:</span><span>Add New Project</span></div>
        <div class="field" style="top:69px;left:5px;width:200px;">Main</div>
        <div class="field" style="top:104px;left:5px;width:200px;">Main</div>
        <div class="field" style="top:104px;left:210px;width:192px;height:20px;"></div>
        <div class="field" style="top:141px;left:0;width:137px;">Enter Product Name or SKU to Add</div>
        <div class="btn-sm" style="top:141px;left:141px;width:40px;background:#a9c2e6;">Add to List</div>
        <div class="field" style="top:141px;left:316px;width:54px;">Select Action</div>
        <div class="btn-sm" style="top:141px;left:373px;width:36px;background:var(--panel-bar);">Apply</div>

        <div class="grid">
          <div class="grid__head"><span class="c-box"><i></i></span><span class="c-mark"></span><span class="c-name">Product/SKU</span><span class="c-qty">Qty</span><span class="c-sell">Sell Price</span><span class="c-my">My Price</span></div>
          <div class="grid__row"><span class="c-box"><i></i></span><span class="c-mark">Norvane</span><span class="c-name"><b>Hail Guard 6.5/12.5 Stratus</b><small>NVX-2207</small></span><span class="c-qty"><i>−</i><span>1</span><i>+</i></span><span class="c-sell">$413.00</span><span class="c-my">$ <span>413.00</span></span><span class="c-del"><svg viewBox="0 0 10 12" aria-hidden="true"><path d="M1 2h8M4 1h2M2 3h6l-.6 8H2.6z" fill="none" stroke="var(--icon)" stroke-width="1.2"/></svg></span></div>
          <div class="grid__row"><span class="c-box"><i></i></span><span class="c-mark">Norvane</span><span class="c-name"><b>Screwdriver, Combo, 6-in-1</b><small>NVX-TL-06</small></span><span class="c-qty"><i>−</i><span>5</span><i>+</i></span><span class="c-sell">$9.00</span><span class="c-my">$ <span>5.00</span></span><span class="c-del"><svg viewBox="0 0 10 12" aria-hidden="true"><path d="M1 2h8M4 1h2M2 3h6l-.6 8H2.6z" fill="none" stroke="var(--icon)" stroke-width="1.2"/></svg></span></div>
          <div class="grid__row"><span class="c-box"><i></i></span><span class="c-mark">Norvane</span><span class="c-name"><b>Hand Seamer, Kelvor</b><small>NVX-HS-3310</small></span><span class="c-qty"><i>−</i><span>16</span><i>+</i></span><span class="c-sell">$50.00</span><span class="c-my">$ <span>90.00</span></span><span class="c-del"><svg viewBox="0 0 10 12" aria-hidden="true"><path d="M1 2h8M4 1h2M2 3h6l-.6 8H2.6z" fill="none" stroke="var(--icon)" stroke-width="1.2"/></svg></span></div>
          <div class="grid__row"><span class="c-box"><i></i></span><span class="c-mark">Norvane</span><span class="c-name"><b>Condenser Mounting Brackets, 1/8" Steel, 600Lb Per Pair</b><small>NVX-MB-18</small></span><span class="c-qty"><i>−</i><span>5</span><i>+</i></span><span class="c-sell">$31.00</span><span class="c-my">$ <span>31.00</span></span><span class="c-del"><svg viewBox="0 0 10 12" aria-hidden="true"><path d="M1 2h8M4 1h2M2 3h6l-.6 8H2.6z" fill="none" stroke="var(--icon)" stroke-width="1.2"/></svg></span></div>
        </div>
      </div>
    </div>
  </section>
</body>
</html>
```